Detail Shop Business card design

i need a business card design for my new detailing company called 'Brisk's Polish Works'. i want an all black and white design . simple, direct and to the point. i want the designer to choose a fitting font to match the logothe front should have logo, address, phone and email and the back side should have a slogan and text indicating that we offer services on anything including cars, trucks, motorcycles and RVs. slogan will read "we take pride in your ride"
maybe also very small on the back side the IG icon with Brisks_Polish_Works

phone 208.417.6352
address 3847 E Larkin Ave
Spokane WA 99214
email: BrisksPolish@mailvexo.com

Target Market(s)

all ages , auto enthusiasts

Industry/Entity Type

Automotive

Contact Information for Business Card

the front should have logo, address, phone and email and the back side should have a slogan and text indicating that we offer services on anything including cars, trucks, motorcycles and RVs. slogan will read "we take pride in your ride"

phone 208.417.6352
address 3847 E Larkin Ave
Spokane WA 99214

Colors
000000
ffffff

Requirements
Must have
• bold font and very simple design with good spacing
Nice to have
• anything creative from the designer indicating we service any types of vehicles
Should not have
• any colors ,

```html
<!DOCTYPE html>
<html lang="en">
<head>
<meta charset="utf-8">
<title>Brisk's Polish Works – Business Cards</title>
<link rel="stylesheet" href="https://fonts.googleapis.com/css2?family=Arvo:wght@700&family=Josefin+Slab:wght@600&display=swap">
<style>
  :root {
    --ink: #000000;
    --paper: #ffffff;
    --stage: #e9e9e9;
    --card-w: 700px;
    --card-h: 400px;
  }
  * { box-sizing: border-box; margin: 0; padding: 0; }
  html, body { width: 1200px; height: 900px; overflow: hidden; }
  body {
    background: var(--stage);
    display: flex;
    flex-direction: column;
    align-items: center;
    justify-content: center;
    gap: 40px;
  }
  .card {
    position: relative;
    width: var(--card-w);
    height: var(--card-h);
    background: var(--paper);
    overflow: hidden;
    box-shadow: 0 6px 18px rgba(0,0,0,0.18);
  }

  /* Back card */
  .card-back .swoosh {
    position: absolute;
    inset: 0;
    width: 100%;
    height: 100%;
  }
  .card-back .brand-block {
    position: absolute;
    left: 0; right: 0;
    top: 175px;
    text-align: center;
  }
  .brand-name {
    font-family: 'Arvo', serif;
    font-weight: 700;
    color: var(--ink);
    letter-spacing: 0.5px;
  }
  .card-back .brand-name { font-size: 34px; }
  .card-back .tagline {
    margin-top: 22px;
    font-family: 'Arvo', serif;
    font-weight: 700;
    font-size: 15px;
    letter-spacing: 0.5px;
    color: var(--ink);
  }

  /* Front card */
  .card-front .top {
    position: absolute;
    left: 0; right: 0; top: 0;
    height: 220px;
  }
  .card-front .brand-name {
    position: absolute;
    left: 40px;
    top: 70px;
    width: 220px;
    font-size: 30px;
    line-height: 1.2;
    text-align: center;
  }
  .card-front .slogan {
    position: absolute;
    right: 40px;
    top: 70px;
    font-family: 'Arvo', serif;
    font-weight: 700;
    font-size: 40px;
    line-height: 1.0;
    color: var(--ink);
    text-transform: uppercase;
  }
  .card-front .band {
    position: absolute;
    left: 0; right: 0; bottom: 0;
    height: 180px;
    background: var(--ink);
    color: var(--paper);
    font-family: 'Josefin Slab', serif;
    font-weight: 600;
    font-size: 19px;
    letter-spacing: 0.3px;
  }
  .contact-list {
    position: absolute;
    left: 50px;
    top: 34px;
    list-style: none;
    display: flex;
    flex-direction: column;
    gap: 12px;
  }
  .contact-list li, .address {
    display: flex;
    align-items: center;
    gap: 10px;
  }
  .icon { width: 18px; height: 18px; flex: none; }
  .handle-mark {
    width: 15px; height: 15px;
    border: 2px solid var(--paper);
    flex: none;
    margin: 0 1px;
  }
  .address {
    position: absolute;
    left: 420px;
    top: 80px;
    align-items: flex-start;
  }
  .address .icon { margin-top: 1px; }
</style>
</head>
<body>

  <section class="card card-back" aria-label="Card back">
    <svg class="swoosh" viewBox="0 0 700 400" preserveAspectRatio="none" aria-hidden="true">
      <path d="M0 0 H700 V4 C560 10 420 60 300 110 C190 155 90 185 0 205 Z" fill="var(--ink)"/>
      <path d="M0 205 C90 185 190 155 300 110 C420 60 560 10 700 4 V30 C560 40 420 90 300 140 C190 185 90 210 0 220 Z" fill="#d9d9d9"/>
    </svg>
    <div class="brand-block">
      <p class="brand-name">Brisk's Polish Works</p>
      <p class="tagline">WE TAKE PRIDE IN YOUR RIDE</p>
    </div>
  </section>

  <section class="card card-front" aria-label="Card front">
    <div class="top">
      <p class="brand-name">Brisk's Polish Works</p>
      <p class="slogan">We take pride<br>in your ride</p>
    </div>
    <div class="band">
      <ul class="contact-list">
        <li>
          <svg class="icon" viewBox="0 0 24 24" aria-hidden="true"><path fill="#fff" d="M6.6 2.5l3 .2 1.3 4.6-2 1.6c.9 2.3 2.7 4.2 5 5.2l1.6-2 4.6 1.3.2 3c0 1.4-1.2 2.6-2.7 2.6C9.9 19 5 14.1 4 6.6 3.9 4.9 5 2.6 6.6 2.5z"/></svg>
          <span>208.417.6352</span>
        </li>
        <li>
          <svg class="icon" viewBox="0 0 24 24" aria-hidden="true"><path fill="#fff" d="M2 5h20v14H2z"/><path d="M2.5 5.5l9.5 7.5 9.5-7.5" fill="none" stroke="#000" stroke-width="1.8"/></svg>
          <span>BrisksPolish@mailvexo.com</span>
        </li>
        <li>
          <span class="handle-mark" aria-hidden="true"></span>
          <span>Brisks_Polish_Works</span>
        </li>
      </ul>
      <div class="address">
        <svg class="icon" viewBox="0 0 24 24" aria-hidden="true"><path fill="#fff" d="M12 2a7 7 0 0 0-7 7c0 5 7 13 7 13s7-8 7-13a7 7 0 0 0-7-7zm0 9.5a2.5 2.5 0 1 1 0-5 2.5 2.5 0 0 1 0 5z"/></svg>
        <span>3847 E Larkin Ave<br>Spokane WA 99214</span>
      </div>
    </div>
  </section>

</body>
</html>
```